Business Cards Needed for Innovative Healthcare Marketing Company

We are a marketing company focused on healthcare. Our company is all about rebranding yourself renewing your image and generating results. The phoenix stands for "reborn" or "rising" which we provide new brands for our clients we take their old brands and renew it with creativity and innovation. I am looking for a business card with color dimension. I have attached an example of a card I think has the look and feel of what I am trying to accomplish. I like that the card example has black and grey font colors, I like the font placement and the small logo, I really like the use of the colors on the right those are the colors of my logo. My logo is phoenix so maybe incorporating flames similar to that design. I would like the back a solid color maybe red with an opaque version of the logo and website. As a marketing company I am always open to creative liberty!

Target Market(s)

Doctors and business professionals.

Industry/Entity Type

Marketing

Contact Information for Business Card

Valcorne Health Care Marketing
Marla Tenwick- CEO
#(512)638-2974
email-marla@valcorne.com
website- valcorne.com

Font styles to use
Sans Serif

Colors
ec1f27
f37122
ffc214
fbed22
fbf289
f04a50

Requirements
Must have
• The logo and required information
Nice to have
• icons by the information
Should not have
• child like font

```html
<!DOCTYPE html>
<html lang="en">
<head>
<meta charset="utf-8">
<title>Valcorne Health Care Marketing – Business Card</title>
<link rel="stylesheet" href="https://fonts.googleapis.com/css2?family=Josefin+Sans:wght@300&family=Open+Sans:wght@400;700&display=swap">
<style>
  :root {
    --stage: #000000;
    --card: #1c1c1e;
    --brand-red: #c9252c;
    --brand-orange: #f37122;
    --brand-amber: #f7a21b;
    --name-orange: #e8691f;
    --text-light: #e4e4e4;
    --text-white: #ffffff;
  }
  * { margin: 0; padding: 0; box-sizing: border-box; }
  html, body {
    width: 1200px;
    height: 900px;
    overflow: hidden;
    background: var(--stage);
  }
  .stage {
    position: relative;
    width: 1200px;
    height: 900px;
  }
  .card {
    position: absolute;
    top: 271px;
    width: 457px;
    height: 281px;
    border-radius: 14px;
    background: var(--card);
    overflow: hidden;
  }
  .card--front { left: 137px; }
  .card--back { left: 626px; }

  .brand-mark {
    position: absolute;
    border-radius: 50%;
    background: radial-gradient(circle at 50% 35%, var(--brand-amber), var(--brand-orange) 55%, var(--brand-red));
  }
  .brand-name {
    position: absolute;
    display: flex;
    flex-direction: column;
    font-family: "Josefin Sans", sans-serif;
    font-weight: 300;
    line-height: 1;
    white-space: nowrap;
  }
  .brand-name__main { display: block; }
  .brand-name__sub {
    display: block;
    letter-spacing: 0.3px;
    border-top: 1px solid currentColor;
  }

  /* front */
  .card--front .brand-mark { left: 146px; top: 40px; width: 62px; height: 62px; }
  .card--front .brand-name {
    right: 43px; top: 46px;
    align-items: flex-start;
    color: var(--brand-red);
  }
  .card--front .brand-name__main { font-size: 37px; padding-bottom: 6px; }
  .card--front .brand-name__sub { font-size: 13.6px; padding-top: 6px; }

  .holder {
    position: absolute;
    left: 45px; top: 158px;
    font-family: "Open Sans", sans-serif;
  }
  .holder__name {
    font-size: 16px;
    font-weight: 700;
    color: var(--name-orange);
    line-height: 1.2;
  }
  .holder__role {
    font-size: 12px;
    color: var(--text-light);
    line-height: 1.3;
  }
  .contacts {
    position: absolute;
    left: 267px; top: 190px;
    list-style: none;
    font-family: "Open Sans", sans-serif;
    font-size: 12.5px;
    color: var(--text-light);
  }
  .contacts li {
    display: flex;
    align-items: center;
    height: 19.5px;
  }
  .contacts svg {
    width: 10px; height: 10px;
    margin-right: 9px;
    fill: var(--brand-orange);
    flex: none;
  }

  /* back */
  .card--back .brand-mark { left: 183px; top: 60px; width: 92px; height: 92px; }
  .card--back .brand-name {
    left: 0; right: 0; top: 180px;
    align-items: center;
    color: var(--text-white);
  }
  .card--back .brand-name__main { font-size: 30px; padding-bottom: 4px; }
  .card--back .brand-name__sub { font-size: 11px; padding-top: 5px; }
</style>
</head>
<body>
<main class="stage">
  <section class="card card--front" aria-label="Business card front">
    <span class="brand-mark" aria-hidden="true"></span>
    <p class="brand-name">
      <span class="brand-name__main">VALCORNE</span>
      <span class="brand-name__sub">HEALTH CARE MARKETING</span>
    </p>
    <div class="holder">
      <p class="holder__name">Marla Tenwick</p>
      <p class="holder__role">CEO</p>
    </div>
    <ul class="contacts">
      <li>
        <svg viewBox="0 0 10 10" aria-hidden="true"><path d="M2 0.5 L3.6 0.5 L4.2 3 L3 3.8 C3.6 5.2 4.8 6.4 6.2 7 L7 5.8 L9.5 6.4 L9.5 8 C9.5 9 8.8 9.5 8 9.5 C4 9.2 0.8 6 0.5 2 C0.5 1.2 1 0.5 2 0.5 Z"/></svg>
        (512)638-2974
      </li>
      <li>
        <svg viewBox="0 0 10 10" aria-hidden="true"><path d="M0.5 2 L9.5 2 L9.5 8.5 L0.5 8.5 Z M1 2.6 L5 5.6 L9 2.6" stroke="#1c1c1e" stroke-width="0.8"/></svg>
        marla@valcorne.com
      </li>
      <li>
        <svg viewBox="0 0 10 10" aria-hidden="true"><circle cx="5" cy="5" r="4.6"/><path d="M0.6 5 H9.4 M5 0.5 C3 2.5 3 7.5 5 9.5 M5 0.5 C7 2.5 7 7.5 5 9.5" stroke="#1c1c1e" stroke-width="0.7" fill="none"/></svg>
        www.valcorne.com
      </li>
    </ul>
  </section>

  <section class="card card--back" aria-label="Business card back">
    <span class="brand-mark" aria-hidden="true"></span>
    <p class="brand-name">
      <span class="brand-name__main">VALCORNE</span>
      <span class="brand-name__sub">HEALTH CARE MARKETING</span>
    </p>
  </section>
</main>
</body>
</html>
```